Brightline Energy Product Distribution Brochure

We are looking to have our current brochure for our customers completely redesigned...the idea is to present the relevant information in an attractive way . Our website is brightlineenergyco.example where you can find more information about us. We have included a file with a rough idea of the page order and what each should include but feel free to adapt based on design. The example provided is only for context and doesnt have to be maintained. We will be using the brochure both digitally and in print form. As long as it reads easily and is eye catching, the design can be horizontal or vertical.Final deliverable should be indesign file.

"Our Brands" page: should be limited to one page (space being enough) where it has the header for each one (for example diesel generators) space for one or two lines of text and then the corresponding logos for each of the five categories
Updates

For those asking: the "our brands" page should be a single page layout where there is a header with the corresponding section and space for maybe one line of text followed by the two logos for that category. Each of the product pages should be similar in fashion to the one in the document attached: a photo of the product with some white space and space for the text to be included. We will be posting additional examples today

Target Market(s)

We want to present it to customers both digitally and in print so they can see our products

Industry/Entity Type

Power Generation

Font styles to use
Serif

Requirements
Must have
• Eye catching and able to present the information in a presentable fashion. Rest is up to you.
Nice to have
• Should incorporate the colors of our logo but can also add other depending on design

```html
<!DOCTYPE html>
<html lang="en">
<head>
<meta charset="UTF-8">
<title>Brightline Energy – Distributor Program Guide</title>
<link href="https://fonts.googleapis.com/css2?family=Lato:wght@300;400;900&display=swap" rel="stylesheet">
<style>
  :root {
    --stage: #5e5e5e;
    --paper: #ffffff;
    --paper-shade: #e9e9e9;
    --yellow: #efb71c;
    --yellow-pale: #f6dc92;
    --charcoal: #433f3f;
    --ink-grey: #4a4a4a;
    --photo-dark: #2b2118;
    --photo-warm: #a0672a;
  }
  * { box-sizing: border-box; margin: 0; padding: 0; }
  html, body { width: 1200px; height: 840px; overflow: hidden; }
  body {
    background: var(--stage);
    font-family: "Lato", Arial, sans-serif;
    display: flex; align-items: center; justify-content: center;
  }
  .cover {
    position: relative;
    width: 560px; height: 792px;
    background: linear-gradient(160deg, var(--paper) 35%, var(--paper-shade) 100%);
    box-shadow: 0 14px 30px rgba(0,0,0,.35);
    overflow: hidden;
  }
  .cover-shapes { position: absolute; inset: 0; }
  .brand {
    position: absolute; top: 70px; right: 60px;
    display: flex; align-items: center; gap: 10px;
    font-weight: 400; font-size: 22px; letter-spacing: .5px;
    color: var(--ink-grey); text-transform: uppercase;
  }
  .brand-mark { width: 22px; height: 22px; background: var(--yellow); }
  .title-block { position: absolute; top: 130px; left: 200px; }
  .title-main {
    font-weight: 900; font-size: 34px; color: var(--yellow);
    letter-spacing: 1px; text-transform: uppercase;
  }
  .title-sub {
    font-weight: 300; font-size: 30px; color: var(--ink-grey);
    letter-spacing: 1px; text-transform: uppercase; margin-top: 2px;
  }
  .title-rule { width: 60px; height: 2px; background: var(--ink-grey); margin: 8px 0 10px; }
  .title-range {
    font-weight: 300; font-size: 18px; color: var(--yellow);
    text-transform: uppercase; line-height: 1.3; letter-spacing: .5px;
  }
  .site-url {
    position: absolute; bottom: 42px; left: 120px;
    font-size: 17px; color: var(--ink-grey); letter-spacing: .5px;
  }
</style>
</head>
<body>
  <article class="cover">
    <svg class="cover-shapes" viewBox="0 0 560 792" width="560" height="792">
      <defs>
        <linearGradient id="photoTone" x1="0" y1="0" x2="1" y2="1">
          <stop offset="0" stop-color="#d8d6d0"/>
          <stop offset="0.45" stop-color="var(--photo-warm)"/>
          <stop offset="1" stop-color="var(--photo-dark)"/>
        </linearGradient>
      </defs>
      <polygon class="accent-pale" points="400,330 560,210 560,330" fill="var(--yellow-pale)"/>
      <polygon class="accent-pale-light" points="470,330 560,270 560,330" fill="#fbe9b8"/>
      <polygon class="accent-band" points="40,292 560,318 560,354 56,322" fill="var(--yellow)"/>
      <polygon class="spine-shade" points="0,270 44,292 100,655 0,655" fill="var(--charcoal)"/>
      <polygon class="product-photo" points="56,334 560,362 560,510 100,650" fill="url(#photoTone)"
               role="img" aria-label="Photo of a white enclosed diesel generator set inside an industrial plant"/>
      <rect class="accent-tab" x="100" y="652" width="62" height="8" fill="var(--yellow)"/>
    </svg>

    <div class="brand"><span>Brightline Energy</span><span class="brand-mark"></span></div>

    <div class="title-block">
      <h1 class="title-main">Distributor</h1>
      <h2 class="title-sub">Program Guide</h2>
      <div class="title-rule"></div>
      <p class="title-range">Diesel Generators,<br>Alternators &amp; Parts</p>
    </div>

    <p class="site-url">www.brightlineenergyco.example</p>
  </article>
</body>
</html>
```